Vibrant, yet professional, stationery set and other designs required.

I need to source a fantastic designer for a new project as part of my company using a new logo designed via sketch harbor.

**UPDATE** I am not looking for just 'fine' design that will suffice. I am looking for something great.

We are a life assurance brokerage based in Dublin, Ireland and BrightRoost.ie is our new website aimed at providing services for young families in Ireland. We are hoping to be the 'Velro' level of service providers in this area and I am looking for the quality of design to reflect this :-) Hopefully that makes sense!

I have a preference for straight lines over curves and waves.

I need...

1. Business card
2. Letterhead
3. Banner (for printing - 76cm X 305cm)
4. Car branding for KORVA 9 (2014 sport model) I believe the templates are freely available online.

Target Market(s)

Parents in Ireland - Aged 27 to 50.

Industry/Entity Type

Financial Planning

Colors

Designer to choose colors to be used in the design.

Requirements
Must have
• All of the items listed in the description above. I like clean, bright, legible, vibrant and professional design.
Should not have
• No silly or 'cheap' looking designs. This is a professional company looking to provide a professional service.

```html
<!DOCTYPE html>
<html lang="en">
<head>
<meta charset="utf-8">
<title>BrightRoost.ie Business Card</title>
<link rel="stylesheet" href="https://fonts.googleapis.com/css2?family=Roboto:wght@400;500;700&display=swap">
<style>
  :root {
    --backdrop: #a3a3a3;
    --brand-orange: #f08119;
    --card-white: #f2f2f2;
    --slate: #8d989b;
    --logo-grey: #7d888c;
    --ink-white: #ffffff;
  }
  * { margin: 0; padding: 0; box-sizing: border-box; }
  html, body {
    width: 1200px; height: 960px; overflow: hidden;
    background: var(--backdrop);
    font-family: "Roboto", Arial, sans-serif;
  }
  .canvas { position: relative; width: 1200px; height: 960px; }

  .card { position: absolute; width: 602px; height: 342px; }

  .card--front {
    left: 320px; top: 106px;
    background: var(--brand-orange);
    color: var(--ink-white);
  }
  .brand-name {
    position: absolute; left: 0; right: 0;
    text-align: center; font-weight: 500; letter-spacing: -1px;
  }
  .card--front .brand-name { top: 178px; font-size: 64px; color: var(--ink-white); }
  .front-url {
    position: absolute; left: 0; right: 0; top: 288px;
    text-align: center; font-size: 14px; letter-spacing: 6px;
  }

  .card--back {
    left: 320px; top: 493px;
    background: var(--card-white);
  }
  .card--back .brand-name { top: 98px; font-size: 62px; color: var(--logo-grey); }
  .brand-dot {
    position: absolute; left: 504px; top: 186px;
    width: 20px; height: 20px; border-radius: 50%;
    background: var(--brand-orange);
  }
  .contact-band {
    position: absolute; left: 0; right: 0; bottom: 0; height: 122px;
    background: var(--slate); color: var(--ink-white);
  }
  .person { position: absolute; left: 29px; top: 14px; }
  .person-name { font-size: 21px; font-weight: 700; }
  .person-role { font-size: 15px; font-weight: 500; margin-top: 2px; }
  .person-address { font-size: 14.5px; line-height: 18px; margin-top: 8px; }
  .contact-list {
    position: absolute; right: 30px; top: 29px;
    list-style: none; font-size: 14.5px; line-height: 19.5px; text-align: right;
  }
  .contact-list li { display: flex; justify-content: flex-end; align-items: center; gap: 10px; }
  .contact-list svg { width: 13px; height: 13px; fill: var(--ink-white); }
</style>
</head>
<body>
<main class="canvas">
  <section class="card card--front">
    <p class="brand-name">brightroost.ie</p>
    <p class="front-url">www.brightroost.ie</p>
  </section>

  <section class="card card--back">
    <p class="brand-name">brightroost.ie</p>
    <span class="brand-dot"></span>
    <div class="contact-band">
      <div class="person">
        <p class="person-name">AIDAN MOORE</p>
        <p class="person-role">CEO/FOUNDER</p>
        <p class="person-address">14 Larkfield Row<br>Rathmines, Dublin D06</p>
      </div>
      <ul class="contact-list">
        <li>014 372 586
          <svg viewBox="0 0 16 16" aria-hidden="true"><path d="M3.5 1l2.5 3-1.5 2a9 9 0 0 0 5 5l2-1.5 3 2.5-1.5 2.5C7 14 2 9 1 2.5z"/></svg></li>
        <li>087 648 9310
          <svg viewBox="0 0 16 16" aria-hidden="true"><path d="M4 0h8v16H4zM5.5 2v10h5V2zM7 13.2h2v1.3H7z" fill-rule="evenodd"/></svg></li>
        <li>014 896 194
          <svg viewBox="0 0 16 16" aria-hidden="true"><path d="M4 1h8v4H4zM1 6h14v6h-3v3H4v-3H1zM5.5 10v3.5h5V10z" fill-rule="evenodd"/></svg></li>
        <li>hello@brightroost.ie
          <svg viewBox="0 0 16 16" aria-hidden="true"><path d="M1 3h14v10H1zM2 4l6 5 6-5z" fill-rule="evenodd"/></svg></li>
      </ul>
    </div>
  </section>
</main>
</body>
</html>
```